business card for a massage therapy practice named 'Cedar and Willow Massage Studio'

I really need a trendy, yet easy on the eyes business card to complement my logo. Ideally with some gold or rose gold foil work.

My uploaded file of the logo I have in horizontal but I have a vertical version as well. Another color that is used in the website is a blush pink here and there. I'd like to see some trendy tropical leaves in the design.

```html
<!DOCTYPE html>
<html lang="en">
<head>
<meta charset="utf-8">
<title>Cedar and Willow Massage Studio – Business Card</title>
<link rel="stylesheet" href="https://fonts.googleapis.com/css2?family=Great+Vibes&family=Work+Sans:wght@400;500&display=swap">
<style>
  :root {
    --backdrop: #2a2a2a;
    --card-black: #1f1f20;
    --card-white: #ffffff;
    --ink: #1a1a1a;
    --gold: #9c8a60;
    --mint: #8fd6c4;
    --wave-dark: #2b2b2d;
  }
  * { box-sizing: border-box; margin: 0; padding: 0; }
  html, body { width: 1200px; height: 930px; overflow: hidden; }
  body {
    background: var(--backdrop);
    font-family: "Work Sans", Arial, sans-serif;
    position: relative;
  }
  .card {
    position: absolute;
    left: 250px;
    width: 700px;
    height: 400px;
    border-radius: 22px;
    overflow: hidden;
  }
  .card-front { top: 45px; background: var(--card-black); }
  .card-back { top: 485px; background: var(--card-white); }

  .brand {
    position: absolute;
    display: flex;
    align-items: center;
    gap: 16px;
  }
  .brand-dot {
    width: 46px; height: 46px;
    border-radius: 50%;
    background: var(--gold);
    flex: none;
  }
  .brand-name {
    font-weight: 500;
    font-size: 26px;
    line-height: 1.15;
    letter-spacing: 0.5px;
  }
  .card-front .brand { left: 50%; top: 50%; transform: translate(-50%, -50%); }
  .card-front .brand-name { color: var(--card-white); }
  .card-back .brand { left: 46px; top: 58px; }
  .card-back .brand-name { color: var(--ink); font-size: 23px; }
  .card-back .brand-dot { width: 40px; height: 40px; }

  .holder-name {
    position: absolute;
    right: 46px;
    top: 140px;
    font-family: "Great Vibes", cursive;
    font-size: 52px;
    color: var(--gold);
    word-spacing: 10px;
  }
  .divider {
    position: absolute;
    left: 200px;
    right: 40px;
    top: 212px;
    height: 2px;
    background: var(--gold);
  }
  .address {
    position: absolute;
    right: 46px;
    top: 228px;
    text-align: right;
    font-size: 15px;
    line-height: 1.35;
    color: var(--ink);
  }
  .contact-list {
    position: absolute;
    left: 200px;
    top: 230px;
    list-style: none;
    font-size: 16px;
    line-height: 1.45;
    color: var(--ink);
  }
  .contact-list li { display: flex; align-items: center; gap: 10px; }
  .contact-list svg { width: 13px; height: 13px; flex: none; }
  .web-accent { color: var(--gold); }
  .wave { position: absolute; left: 0; bottom: 0; width: 700px; height: 400px; }
</style>
</head>
<body>
  <section class="card card-front" aria-label="Card front">
    <div class="brand">
      <span class="brand-dot"></span>
      <span class="brand-name">Cedar and Willow<br>Massage Studio</span>
    </div>
  </section>

  <section class="card card-back" aria-label="Card back">
    <svg class="wave" viewBox="0 0 700 400" aria-hidden="true">
      <path d="M40 400 C300 392 470 292 700 270 L700 400 Z" fill="#9c8a60"/>
      <path d="M60 400 C310 394 480 302 700 282 L700 400 Z" fill="#ffffff"/>
      <path d="M75 400 C320 396 490 310 700 292 L700 400 Z" fill="#2b2b2d"/>
    </svg>

    <div class="brand">
      <span class="brand-dot"></span>
      <span class="brand-name">Cedar and Willow<br>Massage Studio</span>
    </div>

    <p class="holder-name">Marisol Vega</p>
    <div class="divider"></div>
    <p class="address">418 Alder St. suite 210,<br>Fairhaven, CA 95012</p>

    <ul class="contact-list">
      <li>
        <svg viewBox="0 0 16 16"><path d="M4 1 L6.5 4.5 L5 6.5 C6 8.5 7.5 10 9.5 11 L11.5 9.5 L15 12 L13 15 C7 14.5 1.5 9 1 3 Z" fill="#9c8a60"/></svg>
        (555) 014-2738
      </li>
      <li>
        <svg viewBox="0 0 16 16"><rect x="1" y="3" width="14" height="10" rx="1" fill="none" stroke="#9c8a60" stroke-width="1.6"/><path d="M1.5 4 L8 9 L14.5 4" fill="none" stroke="#9c8a60" stroke-width="1.6"/></svg>
        cedarandwillow@mailbox.com
      </li>
      <li>
        <svg viewBox="0 0 16 16"><circle cx="8" cy="8" r="6.5" fill="none" stroke="#9c8a60" stroke-width="1.5"/><ellipse cx="8" cy="8" rx="3" ry="6.5" fill="none" stroke="#9c8a60" stroke-width="1.2"/><path d="M1.5 8 H14.5" stroke="#9c8a60" stroke-width="1.2"/></svg>
        <span>www.<span class="web-accent">cedarandwillow.com</span></span>
      </li>
    </ul>
  </section>
</body>
</html>
```